Webdesign für Heilpraktiker
Zielgruppe
Ich bin Heilpraktiker und betreibe eine Naturheilpraxis mit den Schwerpunkten der traditionellen chinesischen Medizin (TCM). Da ganz besonders in der Philosophie (sogenannte 'Schule' des Wo Shen). Aber auch in der traditionellen Heilweise der TCM, wie Akupunktur, Heilkräutermedizin und weiteres.
Die Zielgruppe sind Menschen, die medizinische Hilfe benötigen. (Vom Kind bis zum älteren Menschen).
Aufgabenstellung
Es gibt ein Heilpraxis Almsee, ein Foto von mir und ggf. ein Landschaftsbild. Ich dachte an fünf Hauptseiten mit Untergruppen. Am Ende sollte alles in Wordpress formatiert werden können, um es zu veröffentlichen.
Weitere Fotos zur Unterstützung der Themen kann ich natürlich gerne liefern.
Die Gestaltung ist nicht festgesetzt. Sollte aber seriös rüber kommen.

```html
<!DOCTYPE html>
<html lang="de">
<head>
<meta charset="utf-8">
<title>Was ist das Wo Shen – Heilpraxis Almsee</title>
<link rel="stylesheet" href="https://fonts.googleapis.com/css2?family=Marcellus&family=Open+Sans:ital,wght@0,300;0,400;1,300&display=swap">
<style>
:root{
  --paper:#f1f0ec;
  --paper-warm:#ebe8df;
  --gold:#bb9c4f;
  --gold-light:#c7aa63;
  --ink:#3a3632;
  --text:#4a4541;
  --dark:#2b2826;
  --stone:#b3ab9a;
  --white:#ffffff;
}
*{margin:0;padding:0;box-sizing:border-box}
html,body{width:1200px;height:3807px;overflow:hidden}
body{position:relative;background:var(--paper);font-family:"Open Sans",sans-serif;color:var(--text)}
.abs{position:absolute}
.brand{left:0;width:1200px;top:20px;text-align:center}
.brand-name{display:inline-flex;align-items:center;gap:14px;font-family:"Marcellus",serif;font-size:30px;color:var(--ink);margin-top:40px}
.brand-dot{width:18px;height:18px;border-radius:50%;background:var(--gold)}
.nav{top:166px;left:0;width:1200px;display:flex;justify-content:center;gap:24px;font-size:18.5px;color:var(--ink);letter-spacing:.3px}
.nav span:nth-child(4){margin-left:6px}
.hero-photo{left:0;top:236px;width:579px;height:385px;background:linear-gradient(160deg,#8a6a3a 0%,#6f7a55 35%,#8d8a80 60%,#2f3a35 100%)}
.hero-band{left:579px;top:272px;width:621px;height:349px;background:var(--gold)}
.quote{left:579px;top:340px;width:640px;text-align:center;color:#f3ead6;font-size:23px;line-height:37px;font-weight:300}
.quote-mark{font-family:"Marcellus",serif;font-size:30px;line-height:0}
.quote-src{font-style:italic;margin-top:12px;font-size:22px}
.section-a{left:0;top:622px;width:1200px;height:504px;background:var(--paper)}
.section-b{left:0;top:1126px;width:1200px;height:1231px;background:var(--paper-warm)}
.section-c{left:0;top:2357px;width:1200px;height:773px;background:var(--paper)}
.heading{font-family:"Marcellus",serif;font-size:25px;color:var(--ink);letter-spacing:.5px;text-align:center;white-space:nowrap}
.copy{font-size:16.5px;line-height:31px;text-align:center;color:var(--text);font-weight:400}
.circle{border-radius:50%}
.credit{font-size:7px;color:#777;white-space:nowrap}
.literature{left:0;top:3130px;width:1200px;height:351px;background:var(--gold-light)}
.literature h2{font-family:"Marcellus",serif;font-weight:400;font-size:32px;color:var(--white);text-align:center;margin-top:44px;letter-spacing:.5px}
.footer{left:0;top:3481px;width:1200px;height:326px;background:var(--dark)}
.footer-badge{left:542px;top:3511px;width:176px;height:176px;border-radius:50%;background:var(--white);display:flex;align-items:center;justify-content:center;font-family:"Marcellus",serif;font-size:19px;color:var(--ink);text-align:center;line-height:24px}
.footer-links{left:0;top:3758px;width:1200px;text-align:center;color:#e8e4dc;font-size:20px;letter-spacing:.4px}
.footer-links span{margin:0 8px}
</style>
</head>
<body>
<div class="abs brand"><div class="brand-name"><span class="brand-dot"></span>Heilpraxis Almsee</div></div>
<nav class="abs nav"><span>STARTSEITE</span><span>ZU MEINER PERSON</span><span>WOBEI KANN ICH HELFEN</span><span>WAS IST DAS WO SHEN</span><span>KONTAKT</span></nav>

<div class="abs hero-photo" role="img" aria-label="Japanischer Garten mit Teich, Felsen und herbstlichen Pflanzen"></div>
<div class="abs hero-band"></div>
<div class="abs quote">
  <div><span class="quote-mark">“</span>Ruhe bringt Gleichgewicht</div>
  <div>und Leichtigkeit.<span class="quote-mark">”</span></div>
  <div class="quote-src">Tian Shuo (370 v. Chr. - 287 v. Chr.)</div>
</div>

<section class="abs section-a"></section>
<h2 class="abs heading" style="left:214px;width:400px;top:716px">WAS IST DAS WO SHEN?</h2>
<p class="abs copy" style="left:110px;width:600px;top:780px">Das Wo Shen ist aus unserer heutigen Sicht ein Ratgeber für ein harmonisches und gesundes Sein, im Zusammenleben mit allen Lebensformen. Es war in all den Jahrtausenden unter anderem ein Anleitungsbuch zum Befragen eines Orakels, eine Handlungsanweisung für chinesische Beamte im 17. Jahrhundert, ein medizinischer Ratgeber, ein Buch über Weltanschauungen<br>und vieles, vieles mehr.<br><br>Im Laufe der heutigen Zeit ist es immer mehr zu einem medizinischen Leitfaden in der Beseitigung von Erkrankungen geworden.</p>
<div class="abs circle" style="left:791px;top:724px;width:310px;height:310px;background:radial-gradient(circle,#3a3430 0 30%,transparent 31%),radial-gradient(circle,transparent 0 36%,#3a3430 37% 60%,transparent 61%)" role="img" aria-label="Yin-Yang-Symbol umgeben von den acht Trigrammen"></div>

<section class="abs section-b"></section>
<h2 class="abs heading" style="left:561px;width:400px;top:1188px">WOHER KOMMT DAS WO SHEN</h2>
<div class="abs circle" style="left:145px;top:1231px;width:212px;height:212px;background:var(--stone)" role="img" aria-label="Yin-Yang-Symbol mit Trigrammen auf grauem Kreis"></div>
<p class="abs copy" style="left:430px;width:650px;top:1241px">Aus heutiger Sicht ist es kaum noch möglich, die genaue Entstehung des Wo Shen in China zu bestimmen. Die Urfassungen sind mehrere Tausend Jahre alt und entwickelten sich in ihrer Deutung immer weiter. Das Wo Shen hat einen großen Teil in der Lebensphilosophie der Menschen in China ausgemacht und diese geprägt. Parallel zum Aufstieg des Konfuzianismus im 17. Jahrhundert zur Staatsideologie wurden auch die Philosophien des Wo Shen immer weiter verankert. Im Jahr 1692 zählte die kaiserliche Staatsbibliothek ca. 2000 Werke, die sich mit dem Wo Shen befassten. Jeder chinesische Philosoph und Gelehrter beschäftigte sich mit diesem Thema und verfasste stellenweise auch seine eigenen Werke.</p>
<p class="abs copy" style="left:100px;width:596px;top:1575px">Anfang des 20. Jahrhunderts war es dann der deutsche Missionar Konrad Albrecht, der, in China lebend, sich der Übersetzung und Deutung des Wo Shen widmete. Er verfasste das erste Werk, das in deutscher Sprache erhältlich war. Natürlich kann man sich vorstellen, dass die chinesische Medizin sehr durch die Philosophie des Wo Shen geprägt wurde. Die Praxis der chinesischen Medizin beruht auf der Erkenntnis solcher Wandlungsmuster, die auch im philosophischen Wo Shen beschrieben sind. Es geht um den harmonischen Verlauf der Körpervorgänge. Eine Unharmonie führt zu Hemmnissen und zu Erkrankungen.</p>
<div class="abs credit" style="left:166px;top:1870px">Bildnachweis: Archiv der Praxis, Porträt um 1920, freie Lizenz zur Verwendung</div>
<div class="abs circle" style="left:850px;top:1599px;width:216px;height:216px;background:radial-gradient(circle at 50% 40%,#8a8682,#3d3a37)" role="img" aria-label="Historisches Schwarzweiß-Porträt des Übersetzers"></div>
<div class="abs circle" style="left:140px;top:1988px;width:216px;height:216px;background:#f4f3f1;border:1px solid #ddd" role="img" aria-label="Historische Tuschezeichnung eines chinesischen Kaisers"></div>
<div class="abs credit" style="left:77px;top:2235px">Bildnachweis: Archiv der Praxis, historische Zeichnung, gemeinfrei</div>
<p class="abs copy" style="left:548px;width:600px;top:1983px">Man kann heutzutage davon ausgehen, dass eines der Hauptwerke der chinesischen Medizin von Shen Lao, der Klassiker des Gelben Kaisers zur inneren Medizin, ca. 2600 v. Chr., stark von dem Wo Shen geprägt worden ist. Das gilt auch für viele Tausende Werke, die davor und danach zum Thema der gesunden Lebensführung und Gesundheit entstanden sind.<br>Das Wo Shen beschreibt mögliche Ursachen von Erkrankungen und gibt auch Vorschläge, diese zu beheben. Eine Philosophie, die so viele Tausende von Jahren existiert, unterliegt natürlich einer steten Weiterentwicklung.</p>

<section class="abs section-c"></section>
<h2 class="abs heading" style="left:114px;top:2445px;text-align:left">DAS WO SHEN AUS HEUTIGER SICHT</h2>
<p class="abs copy" style="left:52px;width:594px;top:2505px">Anfang der 2000er-Jahre haben sich Clara Ashford und Helga Mertens in den Vereinigten Staaten zu einem Projekt zusammengeschlossen und aufgrund ihrer Begeisterung für das Wo Shen viel Neues herausgefunden. Beide blickten schon seinerzeit auf viele Jahrzehnte Erfahrungen mit dem Wo Shen und dessen Anwendung und Interpretation zurück. Sie beschrieben die einzelnen Hexagramme in verständlichen Worten und kamen aufgrund ihrer Forschung zu einer weiteren Möglichkeit der Kommunikation mit vorhandenem Wissen.</p>
<div class="abs circle" style="left:838px;top:2478px;width:216px;height:216px;background:radial-gradient(circle at 65% 35%,#e8dcae 0 18%,#3b2418 19% 55%,#1c1714 56%)" role="img" aria-label="Lavendel neben einer Tiegel mit Heilsalbe"></div>
<div class="abs circle" style="left:106px;top:2789px;width:216px;height:216px;background:radial-gradient(circle at 40% 40%,#e2d7c8,#bfae98)" role="img" aria-label="Geharkter Sand in einem Zen-Garten"></div>
<p class="abs copy" style="left:531px;width:560px;top:2898px">Ich möchte mich bei den Damen für eine über Jahrzehnte gehende Freundschaft und den vielen Unterweisungen bedanken,<br>die ich erhalten durfte.</p>

<section class="abs literature"><h2>EMPFOHLENE LITERATUR</h2></section>

<footer class="abs footer"></footer>
<div class="abs footer-badge">Heilpraxis<br>Almsee</div>
<div class="abs footer-links"><span>IMPRESSUM</span><span>DATENSCHUTZ</span></div>
</body>
</html>
```